Redesign of Form/Document Navigation Page

I need a redesign of our document and navigation bar on the left. We want the same navigation bar layout/setup but want the buttons and typography to be simple and matching all over. The form needs to be aesthetically pleasing and fit within the page.

1st attachment is our Direct Deposit and the second is the form continued.

```html
<!DOCTYPE html>
<html lang="en">
<head>
<meta charset="utf-8">
<title>Employee Direct Deposit Enrollment</title>
<link href="https://fonts.googleapis.com/css2?family=Open+Sans:wght@400;600;700&display=swap" rel="stylesheet">
<style>
:root{
  --blue:#2a5ea8;
  --navy:#1f4e96;
  --gold:#f2a900;
  --page:#eceef2;
  --white:#ffffff;
  --text:#6d7380;
  --muted:#9aa0aa;
  --line:#dde1e7;
}
*{box-sizing:border-box;margin:0;padding:0}
html,body{width:1200px;height:2208px;overflow:hidden}
body{font-family:"Open Sans",Arial,sans-serif;background:var(--page);color:var(--text);position:relative}

.topbar{position:absolute;left:0;top:0;width:1200px;height:80px;background:var(--white);border-bottom:1px solid var(--line)}
.brand{position:absolute;left:20px;top:22px;display:flex;align-items:center;gap:10px}
.brand-mark{width:30px;height:30px;background:var(--gold)}
.brand-name{font-weight:700;font-size:17px;color:var(--blue);letter-spacing:.5px;line-height:1.1;width:150px}
.topnav{position:absolute;left:296px;top:30px;font-size:15px;display:flex;gap:14px;color:var(--muted)}
.topnav a{color:var(--text);text-decoration:none}
.topnav a.current{color:var(--blue);font-weight:600;border-bottom:2px solid var(--gold);padding-bottom:4px}
.user{position:absolute;right:30px;top:30px;font-size:15px;color:var(--blue);font-weight:600}

.sidenav{position:absolute;left:20px;top:160px;width:360px;background:var(--white)}
.nav-item{height:128px;display:flex;align-items:center;gap:22px;padding:0 28px;border-bottom:1px solid var(--line)}
.nav-item svg{width:44px;height:44px;flex:none}
.nav-title{font-size:15px;font-weight:600;color:var(--blue)}
.nav-sub{font-size:12px;color:var(--muted);margin-top:4px}
.nav-item.active{background:var(--gold)}
.nav-item.active .nav-title,.nav-item.active .nav-sub{color:var(--white)}

.panel{position:absolute;left:400px;top:160px;width:780px;height:1920px;background:var(--white);padding:0 30px}
.panel > *{position:absolute;left:30px;right:30px}
h1,h2{color:var(--blue);font-weight:700}
h1{font-size:20px}
h2{font-size:19px}
p{font-size:13.5px;line-height:22px;color:var(--text)}
.label{font-size:14px;color:var(--blue);font-weight:600}

.upload{display:flex;height:42px}
.upload .file{flex:1;background:#f7f8fa;border:1px solid var(--line);display:flex;align-items:center;gap:10px;padding:0 16px;font-size:14px;color:var(--muted)}
.btn{background:var(--blue);color:var(--white);font-weight:700;font-size:14px;display:flex;align-items:center;justify-content:center}
.upload .btn{width:168px}
.refresh{text-align:right;font-size:13px;color:var(--text)}

.radios{display:flex;gap:36px;align-items:center;font-size:14px;color:var(--text)}
.radio{display:flex;align-items:center;gap:10px}
.radio i{width:18px;height:18px;border:1px solid #b8bec8;border-radius:50%;display:block}
.radio.on i{border:5px solid var(--gold)}
.row{display:flex;gap:24px}
.field{flex:1;height:46px;border:1px solid var(--line);display:flex;align-items:center;justify-content:space-between;padding:0 18px;font-size:14px;color:var(--text)}
.field.half{flex:none;width:348px}
.amount{width:70px;height:40px;border:1px solid var(--line);display:flex;align-items:center;justify-content:center;font-size:14px}

.box{border:1px solid var(--line);position:absolute}
.accept{width:224px;height:52px;background:var(--navy)}

.footer{position:absolute;top:2160px;left:20px;right:20px;display:flex;justify-content:space-between;font-size:14px;color:var(--text)}
</style>
</head>
<body>

<header class="topbar">
  <div class="brand"><span class="brand-mark"></span><span class="brand-name">HARBOR WATCH SERVICES</span></div>
  <nav class="topnav"><a class="current" href="#">Home</a><span>|</span><a href="#">Help</a></nav>
  <div class="user">As Admin ▾</div>
</header>

<aside class="sidenav">
  <div class="nav-item active">
    <svg viewBox="0 0 44 44"><rect x="6" y="12" width="32" height="20" rx="2" fill="none" stroke="#fff" stroke-width="3"/><path d="M14 22l5 5 11-11" fill="none" stroke="#fff" stroke-width="3"/></svg>
    <div><div class="nav-title">Direct Deposit</div><div class="nav-sub">Update your details here</div></div>
  </div>
  <div class="nav-item">
    <svg viewBox="0 0 44 44"><path d="M34 22a12 12 0 1 1-4-9" fill="none" stroke="#f2a900" stroke-width="5"/><path d="M26 8l8 4-3 8z" fill="#f2a900"/></svg>
    <div><div class="nav-title">Change W-4</div><div class="nav-sub">Update your details here</div></div>
  </div>
  <div class="nav-item">
    <svg viewBox="0 0 44 44"><rect x="9" y="5" width="26" height="34" fill="none" stroke="#f2a900" stroke-width="3"/><path d="M14 14h16M14 20h16M14 26h16M14 32h10" stroke="#f2a900" stroke-width="2.5"/></svg>
    <div><div class="nav-title">Labour Code</div><div class="nav-sub">Update your details here</div></div>
  </div>
  <div class="nav-item">
    <svg viewBox="0 0 44 44"><circle cx="22" cy="22" r="17" fill="#f2a900"/><rect x="20" y="19" width="4" height="13" fill="#fff"/><circle cx="22" cy="13" r="2.5" fill="#fff"/></svg>
    <div><div class="nav-title">Personal Information</div><div class="nav-sub">Update your details here</div></div>
  </div>
  <div class="nav-item">
    <svg viewBox="0 0 44 44"><rect x="8" y="7" width="28" height="32" fill="#f2a900"/><rect x="16" y="4" width="12" height="7" fill="#fff" stroke="#f2a900" stroke-width="2"/><path d="M14 20h16M14 26h16M14 32h10" stroke="#fff" stroke-width="2.5"/></svg>
    <div><div class="nav-title">Appraisal and Review</div><div class="nav-sub">Update your details here</div></div>
  </div>
  <div class="nav-item">
    <svg viewBox="0 0 44 44"><rect x="6" y="10" width="26" height="28" fill="none" stroke="#f2a900" stroke-width="3"/><path d="M20 28l16-16 4 4-16 16h-4z" fill="#f2a900"/></svg>
    <div><div class="nav-title">Write Up: Slip</div><div class="nav-sub">Update your details here</div></div>
  </div>
  <div class="nav-item">
    <svg viewBox="0 0 44 44"><circle cx="22" cy="14" r="8" fill="#f2a900"/><path d="M8 40c0-10 6-15 14-15s14 5 14 15z" fill="#f2a900"/></svg>
    <div><div class="nav-title">Employee Performance</div><div class="nav-sub">Update your details here</div></div>
  </div>
</aside>

<main class="panel">
  <h1 style="top:20px">Employee Direct Deposit Enrollment Form</h1>
  <p style="top:66px">Use this form to set up, change or cancel direct deposit of your net pay into a checking or savings account. Complete every field, attach the required document and submit the form to payroll at least ten business days before the pay date when the change should take effect.</p>

  <h2 style="top:162px">Attach a Voided check or Bank Deposit Enrollment Form</h2>
  <div class="upload" style="top:208px">
    <div class="file"><svg width="18" height="14" viewBox="0 0 18 14"><path d="M0 1h7l2 2h9v11H0z" fill="#f2a900"/></svg>Browse Your File</div>
    <div class="btn">SEARCH</div>
  </div>
  <div class="refresh" style="top:256px">Refresh</div>

  <h2 style="top:294px">Account Information</h2>
  <p style="top:336px">Enter your bank details exactly as they appear on your check. Your routing transit number is the nine digit number printed at the lower left of the check, followed by your account number. Ask your bank if you are not sure which numbers to use.</p>

  <h2 style="top:432px">Notify Payroll Immediately If You Close or Change Bank Account</h2>
  <div class="radios" style="top:490px">
    <span class="radio on"><i></i>New Enrollment</span>
    <span class="radio"><i></i>Change Enrollment</span>
    <span class="radio"><i></i>Cancel Enrollment</span>
  </div>
  <div class="row" style="top:550px"><div class="field">Bank name <span>▾</span></div><div class="field">City <span>▾</span></div></div>
  <div class="row" style="top:620px"><div class="field">State <span>▾</span></div><div class="field">Routing Transit <span>▾</span></div></div>
  <div class="row" style="top:690px"><div class="field half">Account Number</div></div>
  <div class="radios" style="top:752px">
    <span class="radio"><i></i>New Enrollment</span>
    <span class="radio"><i></i>Change Enrollment</span>
    <span>Amount</span><span class="amount">100%</span>
  </div>

  <h2 style="top:840px">Important : Please read and sign before comleting and submitting</h2>
  <p style="top:894px">I authorize the company to deposit my pay into the account named above and, if needed, to correct any amount deposited in error. This authorization stays in effect until payroll receives written notice from me to change or cancel it, in enough time to act on the request. I understand that the first deposit may be delayed while the account is verified and that a paper check will be issued until then. I agree to notify payroll at once if I close the account or change banks, and I accept that the company is not responsible for delays caused by incorrect information supplied on this form.</p>
  <p style="top:1052px">By signing below I confirm that the information provided is correct and that I have read and understood the terms of this direct deposit agreement.</p>

  <div class="label" style="top:1286px">Employee Name</div>
  <div style="top:1338px;font-size:14px">Employee Signature</div>
  <div class="box" style="left:30px;top:1372px;width:380px;height:40px"></div>
  <div class="box" style="left:30px;top:1426px;width:380px;height:140px"></div>
  <div style="left:440px;top:1400px;font-size:14px">Sign Date</div>
  <div class="box" style="left:520px;top:1386px;width:230px;height:44px"></div>

  <div class="btn accept" style="left:30px;top:1708px">Accept Document</div>
</main>

<footer class="footer">
  <span>© 2018 Company Name &nbsp;|&nbsp; All Rights Reserved</span>
  <span>Privacy Policy &nbsp;|&nbsp; Terms Of Use</span>
</footer>

</body>
</html>
```